Business Card Design for Flood Rescue 360 - Property Restoration Professionals

I need a business card designed for Flood Rescue 360. We are a full-service property restoration solution. Providing water, fire, smoke & storm restoration as well as mold remediation and full remodel or reconstruction to homes and businesses across Dallas-Fort Worth, TX.
Target Market(s)
home and business owners with insurance covered property damage from water, fire or storm related damage
Industry/Entity Type
property restoration
Contact Information for Business Card
Marcus Pelley General Manager Cell: 214-555-0193 Office: 469-555-0148 email: Marcus@FloodRescue360.example services: Water, Fire, Mold, Reconstruction Tagline: Fast Help When the Water Rises!
Look and feel
Each slider illustrates characteristics of the customer's brand and the style your logo design should communicate.

```html
<!DOCTYPE html>
<html lang="en">
<head>
<meta charset="utf-8">
<title>Flood Rescue 360 – Business Card</title>
<link rel="stylesheet" href="https://fonts.googleapis.com/css2?family=Montserrat:wght@400;500;600;700;800&display=swap">
<style>
  :root {
    --brand-blue: #00b2e6;
    --brand-grey: #6f7270;
    --card-black: #141414;
    --card-white: #ffffff;
    --ink: #1b1b1b;
    --backdrop: #ecebe9;
    --font-main: "Montserrat", Arial, sans-serif;
  }
  * { box-sizing: border-box; margin: 0; padding: 0; }
  html, body { width: 1200px; height: 768px; overflow: hidden; }
  body {
    background: var(--backdrop);
    font-family: var(--font-main);
    position: relative;
  }
  .card {
    position: absolute;
    top: 235px;
    width: 520px;
    height: 297px;
    overflow: hidden;
    box-shadow: 0 10px 28px rgba(0,0,0,0.18);
  }
  .card-front { left: 60px; background: var(--card-black); }
  .card-back  { left: 620px; background: var(--card-white); }

  .brand {
    display: flex;
    align-items: center;
    gap: 14px;
  }
  .brand-name {
    color: var(--brand-blue);
    font-weight: 800;
    text-transform: uppercase;
    line-height: 0.92;
    letter-spacing: -0.5px;
    white-space: nowrap;
  }
  .brand-mark {
    border: 6px solid var(--brand-grey);
    border-radius: 50%;
    flex: none;
  }

  .card-front .brand {
    position: absolute;
    left: 70px;
    top: 70px;
  }
  .card-front .brand-name { font-size: 50px; }
  .card-front .brand-mark { width: 92px; height: 92px; border-width: 8px; }
  .tagline {
    position: absolute;
    left: 70px;
    top: 218px;
    color: var(--brand-blue);
    font-weight: 700;
    font-size: 13px;
    letter-spacing: 0.3px;
  }

  .card-back .brand {
    position: absolute;
    left: 24px;
    top: 58px;
    gap: 8px;
  }
  .card-back .brand-name { font-size: 27px; }
  .card-back .brand-mark { width: 48px; height: 48px; border-width: 4px; }

  .bands { position: absolute; left: 0; top: 0; }
  .services {
    position: absolute;
    left: 60px;
    top: 196px;
    color: var(--card-white);
    font-size: 11.5px;
    font-weight: 600;
    letter-spacing: 0.2px;
  }

  .divider {
    position: absolute;
    left: 262px;
    top: 58px;
    width: 2px;
    height: 122px;
    background: var(--brand-blue);
  }
  .contact {
    position: absolute;
    left: 280px;
    top: 60px;
    color: var(--ink);
  }
  .contact-name {
    color: var(--brand-blue);
    font-weight: 700;
    font-size: 21px;
    line-height: 1.1;
  }
  .contact-role {
    font-size: 11.5px;
    margin-bottom: 10px;
  }
  .contact-line {
    display: flex;
    align-items: center;
    gap: 7px;
    font-size: 11.5px;
    line-height: 1.7;
  }
  .contact-line svg { width: 11px; height: 11px; flex: none; fill: var(--brand-blue); }
</style>
</head>
<body>

<section class="card card-front" aria-label="Card front">
  <div class="brand">
    <div class="brand-name">Flood<br>Rescue 360</div>
    <div class="brand-mark" aria-hidden="true"></div>
  </div>
  <p class="tagline">Fast Help When the Water Rises!</p>
</section>

<section class="card card-back" aria-label="Card back">
  <svg class="bands" width="520" height="297" viewBox="0 0 520 297" aria-hidden="true">
    <polygon points="0,185 330,185 302,222 0,222" fill="var(--brand-blue)"/>
    <polygon points="318,232 520,232 520,268 290,268" fill="var(--brand-grey)"/>
  </svg>

  <div class="brand">
    <div class="brand-name">Flood<br>Rescue 360</div>
    <div class="brand-mark" aria-hidden="true"></div>
  </div>

  <p class="services">• Water • Fire • Mold • Reconstruction</p>

  <div class="divider" aria-hidden="true"></div>

  <div class="contact">
    <h1 class="contact-name">Marcus Pelley</h1>
    <p class="contact-role">General Manager</p>
    <p class="contact-line">
      <svg viewBox="0 0 24 24" aria-hidden="true"><path d="M6.6 10.8a15.1 15.1 0 0 0 6.6 6.6l2.2-2.2c.3-.3.7-.4 1-.2 1.1.4 2.3.6 3.6.6.6 0 1 .4 1 1V20c0 .6-.4 1-1 1C10.6 21 3 13.4 3 4c0-.6.4-1 1-1h3.5c.6 0 1 .4 1 1 0 1.3.2 2.5.6 3.6.1.3 0 .7-.2 1z"/></svg>
      214-555-0193
    </p>
    <p class="contact-line">
      <svg viewBox="0 0 24 24" aria-hidden="true"><path d="M4 8c0-2 4-4 8-4s8 2 8 4v2h-4V8.5c-1-.6-2.4-.9-4-.9s-3 .3-4 .9V10H4z"/><rect x="5" y="12" width="14" height="8" rx="1.5"/></svg>
      469-555-0148
    </p>
    <p class="contact-line">
      <svg viewBox="0 0 24 24" aria-hidden="true"><path d="M2 5h20v14H2z" fill="var(--brand-blue)"/><path d="M3 6l9 7 9-7" fill="none" stroke="#fff" stroke-width="1.6"/></svg>
      Marcus@FloodRescue360.example
    </p>
  </div>
</section>

</body>
</html>
```